A flyer for future customers to get acquainted with our company

The flyer/card is intended for intermediaries. The purpose of this flyer is to introduce businesses to Valdro.

It should convey: real estate and financing, with actual images. Various keywords describing what we do: project financing, temporary real estate financing, real estate financing, investment properties, transformations. We distinguish ourselves by being fast, flexible, and personal.

Please ensure the front has an attractive and inviting appearance, and leave space on the back for additional text.

Color codes: #E85B35 en #091E33

```html
<!DOCTYPE html>
<html lang="nl">
<head>
<meta charset="utf-8">
<title>Valdro – flyer voor- en achterkant</title>
<link href="https://fonts.googleapis.com/css2?family=Poppins:wght@300;400;500;600;700;800&display=swap" rel="stylesheet">
<style>
:root{
  --orange:#E85B35;
  --navy:#091E33;
  --grey:#e4e4e6;
  --grey-ring:#ebebed;
  --page:#cfd0d2;
  --white:#ffffff;
  --ink:#1b2534;
}
*{box-sizing:border-box;margin:0;padding:0}
html,body{width:750px;height:1200px;overflow:hidden;background:var(--page);font-family:"Poppins",sans-serif;color:var(--navy)}
.card{position:absolute;left:35px;width:680px;height:453px;background:var(--white);overflow:hidden;box-shadow:0 10px 22px rgba(0,0,0,.22)}
.card--front{top:95px}
.card--back{top:640px}
.abs{position:absolute}
.brand{font-weight:700;color:var(--navy);letter-spacing:-.5px;display:flex;align-items:center;gap:5px}
.brand-dot{width:8px;height:8px;border-radius:50%;background:var(--orange)}

/* front */
.front-sky{left:0;top:0;width:680px;height:200px;background:linear-gradient(180deg,#f4f5f7 0%,#e9ebee 100%)}
.front .brand{left:35px;top:34px;font-size:36px;line-height:1}
.headline{left:35px;top:92px;font-size:21px;font-weight:800;line-height:1.14;letter-spacing:-.2px}
.headline .accent{color:var(--orange)}
.navy-band{left:0;top:199px;width:680px;height:135px;background:var(--navy)}
.orange-pill{left:0;top:183px;width:290px;height:29px;background:var(--orange);border-radius:0 16px 16px 0;color:var(--white);font-weight:700;font-size:13.5px;line-height:29px;padding-left:38px}
.intro{left:38px;top:228px;width:370px;color:var(--white);font-size:8.4px;line-height:1.3;font-weight:400}
.promise{left:38px;top:273px;width:400px;color:var(--white);font-size:10px;font-weight:600;line-height:1.3;border-left:2px solid var(--orange);padding-left:7px}
.ring-grey{left:372px;top:-61px;width:388px;height:388px;border-radius:50%;background:var(--grey-ring)}
.ring-orange{left:387px;top:-46px;width:358px;height:358px;border-radius:50%;background:var(--orange)}
.photo{left:460px;top:-35px;width:306px;height:306px;border-radius:50%;background:radial-gradient(circle at 55% 60%,#d9d4cf 0%,#8c8a88 35%,#2a3140 70%,#141b27 100%)}
.services{left:0;top:333px;width:680px;height:52px;display:flex;gap:4px}
.service{flex:1;background:var(--grey);border-radius:0 0 8px 8px;position:relative;display:flex;align-items:flex-end;justify-content:center;padding-bottom:7px;text-align:center;font-size:9.2px;font-weight:500;line-height:1.2;color:var(--ink)}
.service:first-child{border-radius:0 0 8px 0}
.service:last-child{border-radius:0 0 0 8px}
.service-icon{position:absolute;top:-17px;left:50%;margin-left:-17px;width:34px;height:34px;border-radius:50%;background:var(--orange);border:2.5px solid #d7d8db;display:flex;align-items:center;justify-content:center}
.contact-row{left:35px;top:408px;display:flex;gap:16px;font-size:11px;font-weight:500;color:var(--ink);align-items:center}
.contact-item{display:flex;align-items:center;gap:3px}
.web-pill{left:500px;top:401px;width:180px;height:29px;background:var(--navy);border-radius:14px 0 0 14px;color:var(--white);font-size:15px;font-weight:600;letter-spacing:2.2px;line-height:29px;padding-left:20px}
.web-pill .accent{color:var(--orange)}

/* back */
.back-ring{left:-70px;top:-99px;width:385px;height:385px;border-radius:50%;background:var(--grey-ring)}
.back-circle{left:-44px;top:-77px;width:344px;height:344px;border-radius:50%;background:var(--orange)}
.back-title{left:30px;top:35px;width:270px;font-size:12.5px;font-weight:700;line-height:1.15;color:var(--navy)}
.back-lead{left:30px;top:66px;width:265px;font-size:7.6px;font-weight:600;color:var(--white);line-height:1.3}
.checklist{left:30px;top:102px;width:250px;list-style:none;color:var(--white);font-size:7.4px;line-height:1.25}
.checklist li{display:flex;gap:4px;margin-bottom:2px}
.checklist svg{flex:none;margin-top:1px}
.usp-bar{left:0;top:172px;width:295px;height:46px;background:var(--navy);border-radius:0 10px 10px 0;color:var(--white);padding:6px 0 0 30px}
.usp-lead{font-size:9.5px;font-weight:400}
.usp-list{display:flex;gap:20px;font-size:12px;font-weight:700;margin-top:1px}
.usp-list span{display:flex;align-items:center;gap:2px}
.section-title{left:25px;top:270px;font-size:14px;font-weight:600}
.section-title .accent{color:var(--orange);font-weight:400}
.svc-grid{left:20px;top:296px;width:260px;display:grid;grid-template-columns:repeat(3,1fr);row-gap:6px}
.svc{display:flex;flex-direction:column;align-items:center;gap:3px;font-size:6.2px;font-weight:600;color:var(--ink)}
.svc-icon{width:32px;height:32px;border-radius:50%;background:var(--navy);border:3px solid var(--orange);box-shadow:0 0 0 2px #cfd0d3;display:flex;align-items:center;justify-content:center}
.call-pill{left:0;top:400px;width:289px;height:29px;background:var(--grey);border-radius:0 15px 15px 0;display:flex;align-items:center;gap:12px;padding-left:37px;font-size:16px;font-weight:500;color:var(--ink)}
.call-pill strong{font-weight:600;display:flex;align-items:center;gap:3px}
.back .brand{left:372px;top:33px;font-size:27px;line-height:1}
.return-address{left:373px;top:84px;font-size:6.6px;line-height:1.3;color:var(--ink)}
.stamp{left:588px;top:37px;width:53px;height:62px;background:#efeff0;border-radius:5px}
.address-line{left:374px;width:266px;height:1px;background:#dcdcdf}
.back-contact{left:341px;top:412px;display:flex;gap:16px;font-size:10.5px;font-weight:500;color:var(--ink)}
</style>
</head>
<body>

<section class="card card--front front" aria-label="Voorkant flyer">
  <div class="abs front-sky" role="img" aria-label="Vervaagde skyline met bouwkranen"></div>
  <div class="abs navy-band"></div>
  <div class="abs ring-grey"></div>
  <div class="abs ring-orange"></div>
  <div class="abs photo" role="img" aria-label="Foto: zakenman houdt een modelhuisje in de hand, met stapels munten en bankbiljetten"></div>

  <div class="abs brand"><span>Valdro</span><span class="brand-dot"></span></div>
  <h1 class="abs headline"><span class="accent">Zoekt u een tijdelijke</span><br>vastgoedfinanciering voor<br>uw zakelijk projecten?</h1>

  <div class="abs orange-pill">En wilt u direct duidelijkheid?</div>
  <p class="abs intro">Als ondernemers in financieringen begrijpen we dat u snel wilt schakelen. Daarom hoort u direct of we u kunnen helpen en kan uw financiering al binnen 5 werkdagen rond zijn. Hoe het werkt, leest u op deze website.</p>
  <p class="abs promise">Vlotte acceptatie, creatieve financieringsoplossingen en maatwerk:<br>Dat is wat we al sinds 2013 doen.</p>

  <div class="abs services">
    <div class="service"><span class="service-icon"><svg width="16" height="16" viewBox="0 0 16 16" fill="#fff"><rect x="1" y="9" width="2.5" height="6"/><rect x="5" y="6" width="2.5" height="9"/><circle cx="12" cy="10" r="3.5"/><path d="M8 4l3-3 3 3h-2v2h-2V4z"/></svg></span>Tijdelijke<br>vastgoedfinancieringen</div>
    <div class="service"><span class="service-icon"><svg width="16" height="16" viewBox="0 0 16 16" fill="#fff"><ellipse cx="6" cy="4" rx="5" ry="2"/><rect x="1" y="5" width="10" height="2.5" rx="1"/><rect x="1" y="8.5" width="10" height="2.5" rx="1"/><circle cx="11.5" cy="11.5" r="4"/></svg></span>Vastgoedfinancieringen</div>
    <div class="service"><span class="service-icon"><svg width="16" height="16" viewBox="0 0 16 16" fill="#fff"><circle cx="9" cy="5" r="4"/><path d="M1 11h4l3 1.5h4l2-1.5v2l-4 2.5H1z"/></svg></span>Projectfinancieringen</div>
    <div class="service"><span class="service-icon"><svg width="16" height="16" viewBox="0 0 16 16" fill="#fff"><path d="M1 8l7-6 7 6h-2v7H3V8z"/></svg></span>Beleggingspanden</div>
    <div class="service"><span class="service-icon"><svg width="16" height="16" viewBox="0 0 16 16" fill="none" stroke="#fff" stroke-width="2"><path d="M3 8a5 5 0 0 1 9-3"/><path d="M13 8a5 5 0 0 1-9 3"/><path d="M12 2v3h-3M4 14v-3h3" stroke-width="1.6"/></svg></span>Transformaties</div>
  </div>

  <div class="abs contact-row">
    <span class="contact-item"><svg width="10" height="10" viewBox="0 0 16 16" fill="var(--orange)"><path d="M4 1l3 3-2 2a9 9 0 0 0 5 5l2-2 3 3-2 3C7 15 1 9 1 3z"/></svg>(030) 418 62 90</span>
    <span class="contact-item"><svg width="10" height="8" viewBox="0 0 16 12" fill="var(--orange)"><path d="M0 0h16v12H0z"/><path d="M0 0l8 6 8-6" stroke="#fff" fill="none"/></svg>info@valdro.nl</span>
    <span class="contact-item"><svg width="8" height="11" viewBox="0 0 12 16" fill="var(--orange)"><path d="M6 0a6 6 0 0 1 6 6c0 4-6 10-6 10S0 10 0 6a6 6 0 0 1 6-6z"/><circle cx="6" cy="6" r="2" fill="#fff"/></svg>Havenstraat 14, 3511 KL Utrecht</span>
  </div>
  <div class="abs web-pill">www.<span class="accent">valdro</span>.nl</div>
</section>

<section class="card card--back back" aria-label="Achterkant flyer">
  <div class="abs back-ring"></div>
  <div class="abs back-circle" role="img" aria-label="Oranje cirkel met vervaagde skyline"></div>

  <h2 class="abs back-title">Vastgoedfinanciering voor ondernemers</h2>
  <p class="abs back-lead">Valdro biedt korte termijn financieringen voor vastgoedondernemers die snel kansen willen grijpen. We zijn gespecialiseerd in financieringsvraagstukken:</p>
  <ul class="abs checklist">
    <li><svg width="7" height="7" viewBox="0 0 10 10"><circle cx="5" cy="5" r="5" fill="#fff"/><path d="M2.5 5l1.8 1.8L7.5 3.5" stroke="var(--navy)" stroke-width="1.5" fill="none"/></svg>Voor het handelen in onroerend goed</li>
    <li><svg width="7" height="7" viewBox="0 0 10 10"><circle cx="5" cy="5" r="5" fill="#fff"/><path d="M2.5 5l1.8 1.8L7.5 3.5" stroke="var(--navy)" stroke-width="1.5" fill="none"/></svg>Voor transformatie van kantoorgebouwen<br>naar appartementen</li>
    <li><svg width="7" height="7" viewBox="0 0 10 10"><circle cx="5" cy="5" r="5" fill="#fff"/><path d="M2.5 5l1.8 1.8L7.5 3.5" stroke="var(--navy)" stroke-width="1.5" fill="none"/></svg>Het realiseren van een nieuwbouwcomplex of woningen</li>
    <li><svg width="7" height="7" viewBox="0 0 10 10"><circle cx="5" cy="5" r="5" fill="#fff"/><path d="M2.5 5l1.8 1.8L7.5 3.5" stroke="var(--navy)" stroke-width="1.5" fill="none"/></svg>Het verbouwen van je beleggingspand of<br>commercieel vastgoed</li>
  </ul>

  <div class="abs usp-bar">
    <p class="usp-lead">Wij onderscheiden ons door te zijn</p>
    <div class="usp-list">
      <span><svg width="9" height="9" viewBox="0 0 10 10"><path d="M1 5l3 3 5-6" stroke="#fff" stroke-width="1.6" fill="none"/></svg>Snel</span>
      <span><svg width="9" height="9" viewBox="0 0 10 10"><path d="M1 5l3 3 5-6" stroke="#fff" stroke-width="1.6" fill="none"/></svg>Flexibel</span>
      <span><svg width="9" height="9" viewBox="0 0 10 10"><path d="M1 5l3 3 5-6" stroke="#fff" stroke-width="1.6" fill="none"/></svg>Persoonlijk</span>
    </div>
  </div>

  <h3 class="abs section-title"><span class="accent">Onze</span> diensten</h3>
  <div class="abs svc-grid">
    <div class="svc"><span class="svc-icon"><svg width="14" height="14" viewBox="0 0 16 16" fill="#fff"><path d="M1 6l4-3 3 2 3-2 4 3-4 4-3-2-3 2z"/></svg></span>Handelsfinanciering</div>
    <div class="svc"><span class="svc-icon"><svg width="14" height="14" viewBox="0 0 16 16" fill="#fff"><rect x="3" y="4" width="10" height="11"/><rect x="1" y="1" width="14" height="2"/></svg></span>Bouwfinanciering</div>
    <div class="svc"><span class="svc-icon"><svg width="14" height="14" viewBox="0 0 16 16" fill="#fff"><rect x="1" y="9" width="2.5" height="6"/><rect x="5" y="6" width="2.5" height="9"/><circle cx="12" cy="10" r="3.5"/></svg></span>Beleggingsfinanciering</div>
    <div class="svc"><span class="svc-icon"><svg width="14" height="14" viewBox="0 0 16 16" fill="#fff"><rect x="1" y="1" width="6" height="6"/><rect x="9" y="9" width="6" height="6"/><circle cx="12" cy="4" r="3"/><circle cx="4" cy="12" r="3"/></svg></span>Transformatiefinanciering</div>
    <div class="svc"><span class="svc-icon"><svg width="14" height="14" viewBox="0 0 16 16" fill="#fff"><path d="M2 10a6 6 0 0 1 12 0z"/><rect x="1" y="11" width="14" height="2"/></svg></span>Nieuwbouwfinanciering</div>
    <div class="svc"><span class="svc-icon"><svg width="14" height="14" viewBox="0 0 16 16" fill="#fff"><circle cx="8" cy="7" r="5"/><rect x="4" y="13" width="8" height="2"/></svg></span>Stressfinanciering</div>
  </div>

  <div class="abs call-pill">Call us <strong><svg width="14" height="14" viewBox="0 0 16 16" fill="var(--orange)"><path d="M4 1l3 3-2 2a9 9 0 0 0 5 5l2-2 3 3-2 3C7 15 1 9 1 3z"/></svg>(030) 418 62 90</strong></div>

  <div class="abs brand"><span>Valdro</span><span class="brand-dot"></span></div>
  <p class="abs return-address">Havenstraat 14, 3511<br>KL Utrecht</p>
  <div class="abs stamp" aria-label="Vak voor postzegel"></div>
  <div class="abs address-line" style="top:175px"></div>
  <div class="abs address-line" style="top:224px"></div>
  <div class="abs address-line" style="top:272px"></div>
  <div class="abs address-line" style="top:320px"></div>

  <div class="abs back-contact">
    <span class="contact-item"><svg width="10" height="8" viewBox="0 0 16 12" fill="var(--orange)"><path d="M0 0h16v12H0z"/><path d="M0 0l8 6 8-6" stroke="#fff" fill="none"/></svg>info@valdro.nl</span>
    <span class="contact-item"><svg width="8" height="11" viewBox="0 0 12 16" fill="var(--orange)"><path d="M6 0a6 6 0 0 1 6 6c0 4-6 10-6 10S0 10 0 6a6 6 0 0 1 6-6z"/><circle cx="6" cy="6" r="2" fill="#fff"/></svg>Havenstraat 14, 3511 KL Utrecht</span>
  </div>
</section>

</body>
</html>
```